Redesign our Product Box!

We have a product box for our pet supplement we are looking to redesign. Please use the photoshop file of the current design for the logo/info/dieline and the concept picture of a bag we would like to see included in the box design.

Ideally the background will be the green with white text, but we really want it to be fun and appealing to pet owners so do not be scared to show your vision.

```html
<!DOCTYPE html>
<html lang="en">
<head>
<meta charset="utf-8">
<title>AlgaVita Product Box Dieline</title>
<link rel="stylesheet" href="https://fonts.googleapis.com/css2?family=Source+Sans+3:wght@300;400;600;800&family=Archivo+Black&display=swap">
<style>
  :root{
    --green:#00a54f;
    --green-dark:#009447;
    --cut:#d9302c;
    --fold:#3453a3;
    --ink:#2a2a2a;
    --paper:#ffffff;
    --olive:#8cc04b;
  }
  html,body{margin:0;padding:0;width:1097px;height:1200px;overflow:hidden;background:var(--paper);}
  .dieline{display:block;width:1097px;height:1200px;}
  .dieline text{font-family:"Source Sans 3",sans-serif;fill:var(--ink);}
  .brand{font-weight:800;fill:var(--green)!important;font-size:62px;letter-spacing:-1px;}
  .band-text{fill:#fff!important;font-size:44px;font-weight:400;}
  .body-copy text{font-size:25px;font-weight:300;}
  .directions text{font-size:24px;font-weight:400;}
  .tag-copy{font-size:33px;font-weight:400;}
  .heading{font-size:29px;font-weight:600;}
  .facts-title{font-family:"Archivo Black",sans-serif!important;font-size:36px;}
  .facts-small{font-size:15px;}
  .fine{font-size:11px;}
  .address{font-size:22px;}
  .warning text{font-size:14px;}
  .print-note{font-size:62px;font-weight:400;}
  .panel-id{font-size:26px;font-weight:800;}
  .cut{fill:none;stroke:var(--cut);stroke-width:2;}
  .fold{fill:none;stroke:var(--fold);stroke-width:2;}
  .green-fill{fill:var(--green);}
  .tile{fill:var(--green-dark);opacity:.35;}
</style>
</head>
<body>
<svg class="dieline" viewBox="0 0 1834 2000" preserveAspectRatio="none" xmlns="http://www.w3.org/2000/svg">
  <defs>
    <linearGradient id="petTone" x1="0" y1="0" x2="1" y2="1">
      <stop offset="0" stop-color="#f2e3d4"/>
      <stop offset=".5" stop-color="#d9a273"/>
      <stop offset="1" stop-color="#b86f3a"/>
    </linearGradient>
  </defs>

  <!-- top tuck flap -->
  <path class="cut" d="M205 330 C205 250 240 215 270 198 L562 198 C600 225 627 260 627 330" fill="#fff"/>
  <path class="cut" d="M200 330 L240 330 L243 337 M588 337 L592 330 L632 330"/>
  <line class="fold" x1="243" y1="332" x2="588" y2="332"/>

  <!-- top lid panel -->
  <rect x="200" y="330" width="432" height="345" fill="#fff" class="cut"/>
  <rect x="240" y="430" width="390" height="240" fill="#f4f4f4" opacity=".7"/>
  <text class="brand" x="415" y="520" text-anchor="middle">AlgaVita</text>

  <!-- glue flap -->
  <polygon class="cut" points="92,686 200,676 200,1453 92,1444" fill="#fff"/>

  <!-- top dust flaps -->
  <polygon class="green-fill" points="632,437 935,437 952,628 975,650 975,675 632,675"/>
  <polyline class="cut" points="632,437 935,437 952,628 975,650 975,675"/>
  <polygon class="green-fill" points="1452,437 1750,437 1750,675 1414,675 1414,650 1437,628"/>
  <polyline class="cut" points="1414,675 1414,650 1437,628 1452,437 1750,437 1750,675"/>

  <!-- body panels -->
  <rect x="200" y="675" width="1550" height="778" fill="#fff"/>
  <rect x="200" y="905" width="432" height="115" class="green-fill"/>
  <rect x="200" y="1373" width="1550" height="80" class="green-fill"/>
  <rect x="760" y="1373" width="240" height="80" class="tile"/>
  <rect x="1500" y="1373" width="150" height="80" class="tile"/>

  <!-- bottom flaps -->
  <polygon class="green-fill" points="636,1453 977,1453 977,1692 675,1692 658,1500 636,1480"/>
  <polygon class="green-fill" points="1410,1453 1750,1453 1750,1480 1728,1500 1712,1692 1410,1692"/>
  <polyline class="cut" points="636,1453 636,1480 658,1500 675,1692 977,1692"/>
  <polyline class="cut" points="1410,1692 1712,1692 1728,1500 1750,1480 1750,1453"/>
  <rect x="700" y="1520" width="250" height="150" class="tile"/>
  <rect x="1450" y="1480" width="230" height="130" class="tile"/>

  <!-- bottom panel + tuck -->
  <rect x="977" y="1453" width="433" height="347" class="green-fill"/>
  <path class="green-fill" d="M982 1800 L1406 1800 C1406 1860 1380 1900 1340 1933 L1046 1933 C1005 1900 982 1860 982 1800 Z"/>
  <path class="cut" d="M977 1453 L977 1800 L1020 1800 L1022 1792 M1366 1792 L1368 1800 L1410 1800 L1410 1453"/>
  <path class="cut" d="M982 1800 C982 1860 1005 1900 1046 1933 L1340 1933 C1380 1900 1406 1860 1406 1800"/>
  <line class="fold" x1="1022" y1="1797" x2="1366" y2="1797"/>
  <rect x="1060" y="1480" width="250" height="200" class="tile"/>
  <text class="band-text" x="1198" y="1745" text-anchor="middle" transform="rotate(180 1198 1745)" style="font-size:28px" textLength="340" lengthAdjust="spacingAndGlyphs">Exp: 22025/03/Lot No.:12222</text>

  <!-- folds and cuts on body -->
  <line class="fold" x1="200" y1="675" x2="1750" y2="675"/>
  <line class="fold" x1="200" y1="1453" x2="1750" y2="1453"/>
  <line class="fold" x1="200" y1="676" x2="200" y2="1453"/>
  <line class="fold" x1="632" y1="675" x2="632" y2="1453"/>
  <line class="fold" x1="977" y1="675" x2="977" y2="1453"/>
  <line class="fold" x1="1410" y1="675" x2="1410" y2="1453"/>
  <line class="cut" x1="1750" y1="675" x2="1750" y2="1453"/>
  <line class="cut" x1="632" y1="330" x2="632" y2="437"/>
  <line class="cut" x1="975" y1="675" x2="1414" y2="675"/>

  <!-- front panel -->
  <text class="brand" x="415" y="815" text-anchor="middle">AlgaVita</text>
  <text class="band-text" x="414" y="948" text-anchor="middle" textLength="306" lengthAdjust="spacingAndGlyphs">100% Pure Marine</text>
  <text class="band-text" x="413" y="1000" text-anchor="middle" textLength="389" lengthAdjust="spacingAndGlyphs">Phytoplankton Powder</text>
  <rect x="410" y="1200" width="222" height="173" fill="url(#petTone)" role="img" aria-label="Photo of a corgi puppy and a tabby kitten"/>
  <text class="tag-copy" x="412" y="1085" text-anchor="middle" textLength="300" lengthAdjust="spacingAndGlyphs">Foundational Nutrition</text>
  <text class="tag-copy" x="412" y="1125" text-anchor="middle" textLength="267" lengthAdjust="spacingAndGlyphs">&amp; Super-Antioxidant</text>
  <text class="tag-copy" x="412" y="1187" text-anchor="middle" textLength="205" lengthAdjust="spacingAndGlyphs">For Dogs &amp; Cats</text>
  <text class="band-text" x="415" y="1403" text-anchor="middle" style="font-size:25px">15g</text>

  <!-- directions panel -->
  <g class="directions" text-anchor="middle">
    <text x="806" y="725" textLength="262" lengthAdjust="spacingAndGlyphs">Directions: For dogs &amp; cats</text>
    <text x="806" y="754" textLength="204" lengthAdjust="spacingAndGlyphs">1/16tsp once per day.</text>
    <text x="806" y="783" textLength="299" lengthAdjust="spacingAndGlyphs">Administer orally. To be mixed</text>
    <text x="806" y="812" textLength="257" lengthAdjust="spacingAndGlyphs">into food. 1/16tsp = 1/2 the</text>
    <text x="806" y="841" textLength="156" lengthAdjust="spacingAndGlyphs">included scoop.</text>
  </g>
  <line x1="684" y1="883" x2="928" y2="883" stroke="var(--olive)" stroke-width="2.5"/>
  <text class="heading" x="807" y="915" text-anchor="middle" textLength="170" lengthAdjust="spacingAndGlyphs">Unlock Nature’s</text>
  <text class="heading" x="807" y="950" text-anchor="middle" textLength="196" lengthAdjust="spacingAndGlyphs">Nutrient Treasure:</text>
  <g class="body-copy" text-anchor="middle">
    <text x="807" y="1006" textLength="302" lengthAdjust="spacingAndGlyphs">Phytoplankton is the foundation of</text>
    <text x="807" y="1035" textLength="295" lengthAdjust="spacingAndGlyphs">life, It is the first plant in the entire</text>
    <text x="807" y="1064" textLength="96" lengthAdjust="spacingAndGlyphs">food chain.</text>
    <text x="807" y="1121" textLength="269" lengthAdjust="spacingAndGlyphs">Phytoplankton is a microscopic</text>
    <text x="807" y="1150" textLength="250" lengthAdjust="spacingAndGlyphs">powerhouse. Your pet’s body</text>
    <text x="807" y="1179" textLength="290" lengthAdjust="spacingAndGlyphs">absorbs billions of phytoplankton</text>
    <text x="807" y="1208" textLength="163" lengthAdjust="spacingAndGlyphs">with every serving.</text>
    <text x="807" y="1265" textLength="297" lengthAdjust="spacingAndGlyphs">Packed with the building blocks of</text>
    <text x="807" y="1294" textLength="264" lengthAdjust="spacingAndGlyphs">life, phytoplankton addresses</text>
    <text x="807" y="1323" textLength="252" lengthAdjust="spacingAndGlyphs">multiple aspects of your pet’s</text>
    <text x="807" y="1352" textLength="290" lengthAdjust="spacingAndGlyphs">health in one simple supplement.</text>
  </g>

  <!-- facts panel -->
  <text class="print-note" x="1120" y="503">PRINT</text>
  <text class="print-note" x="1120" y="575">SIDE</text>
  <rect x="1001" y="707" width="389" height="202" fill="#fff" stroke="#222" stroke-width="2.5"/>
  <line x1="1001" y1="758" x2="1390" y2="758" stroke="#222" stroke-width="2.5"/>
  <line x1="1001" y1="810" x2="1390" y2="810" stroke="#222" stroke-width="2.5"/>
  <line x1="1001" y1="869" x2="1390" y2="869" stroke="#222" stroke-width="2.5"/>
  <text class="facts-title" x="1188" y="746" text-anchor="middle" textLength="313" lengthAdjust="spacingAndGlyphs">Supplement Facts</text>
  <text class="facts-small" x="1025" y="783" textLength="153" lengthAdjust="spacingAndGlyphs">Serving Size: 1 Scoop/Day</text>
  <text class="facts-small" x="1025" y="799" textLength="156" lengthAdjust="spacingAndGlyphs">Servings per Container: 30</text>
  <text class="facts-small" x="1214" y="799" textLength="120" lengthAdjust="spacingAndGlyphs">Amount per Serving</text>
  <text class="facts-small" x="1345" y="799" textLength="30" lengthAdjust="spacingAndGlyphs">%DV</text>
  <text class="facts-small" x="1025" y="843" textLength="225" lengthAdjust="spacingAndGlyphs">Microalgae Nannochloropsis Gaditana</text>
  <text class="facts-small" x="1294" y="843" textLength="42" lengthAdjust="spacingAndGlyphs">500mg</text>
  <text class="facts-small" x="1358" y="843">‡</text>
  <text class="facts-small" x="1025" y="893" textLength="184" lengthAdjust="spacingAndGlyphs">‡ Daily value not established.</text>
  <text class="fine" x="1001" y="928" textLength="362" lengthAdjust="spacingAndGlyphs">These statements have not been evaluated by the Food and Drug Administrations.</text>
  <text class="fine" x="1001" y="943" textLength="337" lengthAdjust="spacingAndGlyphs">This products is not intended to diagnose, treat, cure, or prevent any disease.</text>
  <text class="fine" x="1001" y="971" textLength="109" lengthAdjust="spacingAndGlyphs">Store in a cool, dry place.</text>
  <text class="address" x="1004" y="1023" style="font-weight:600" textLength="147" lengthAdjust="spacingAndGlyphs">Distributed By::</text>
  <text class="address" x="1004" y="1049">Marinell Nutrition Inc.</text>
  <text class="address" x="1004" y="1075">42-8 Harbour Road,</text>
  <text class="address" x="1004" y="1101">Saltcove, Nova Scotia Canada</text>
  <text class="address" x="1004" y="1127">B0J 2K0</text>
  <g class="warning">
    <text x="1002" y="1151" textLength="379" lengthAdjust="spacingAndGlyphs">Warnings: Check with a qualified healthcare professional before</text>
    <text x="1002" y="1168" textLength="375" lengthAdjust="spacingAndGlyphs">using this product if you are pregnant, breastfeeding, or taking</text>
    <text x="1002" y="1185" textLength="369" lengthAdjust="spacingAndGlyphs">blood thinners. You should call your doctor for medical advice</text>
    <text x="1002" y="1202" textLength="376" lengthAdjust="spacingAndGlyphs">about serious adverse events. To report a serious adverse event</text>
    <text x="1002" y="1219" textLength="328" lengthAdjust="spacingAndGlyphs">or obtain product information contact:  1 800 555 0142</text>
  </g>
  <text class="band-text" x="1193" y="1406" text-anchor="middle" style="font-size:24px">Customer Care: 1 800 555 0142</text>
  <text class="band-text" x="1193" y="1435" text-anchor="middle" style="font-size:24px">marinellnutrition.com</text>

  <!-- story panel -->
  <g class="body-copy" text-anchor="middle">
    <text x="1577" y="725" textLength="251" lengthAdjust="spacingAndGlyphs">Our premium phytoplankton</text>
    <text x="1577" y="754" textLength="221" lengthAdjust="spacingAndGlyphs">powder is a extraordinary</text>
    <text x="1577" y="783" textLength="285" lengthAdjust="spacingAndGlyphs">supplement.  It infuses your pet’s</text>
    <text x="1577" y="812" textLength="244" lengthAdjust="spacingAndGlyphs">body with pure, plant-based</text>
    <text x="1577" y="841" textLength="296" lengthAdjust="spacingAndGlyphs">nutrients and potent antioxidants.</text>
    <text x="1577" y="898" textLength="246" lengthAdjust="spacingAndGlyphs">Phytoplankton goes beyond</text>
    <text x="1577" y="927" textLength="283" lengthAdjust="spacingAndGlyphs">ordinary supplements; it's a path</text>
    <text x="1577" y="956" textLength="262" lengthAdjust="spacingAndGlyphs">to optimal health. In just a few</text>
    <text x="1577" y="985" textLength="283" lengthAdjust="spacingAndGlyphs">weeks, your pet will experience a</text>
    <text x="1577" y="1014" textLength="280" lengthAdjust="spacingAndGlyphs">feeling of calm and strength, the</text>
    <text x="1577" y="1043" textLength="268" lengthAdjust="spacingAndGlyphs">kind of wellness our customers</text>
    <text x="1577" y="1072" textLength="272" lengthAdjust="spacingAndGlyphs">often say they've been seeking.</text>
    <text x="1577" y="1129" textLength="276" lengthAdjust="spacingAndGlyphs">Join those who have discovered</text>
    <text x="1577" y="1158" textLength="244" lengthAdjust="spacingAndGlyphs">the transformative power of</text>
    <text x="1577" y="1187" textLength="294" lengthAdjust="spacingAndGlyphs">phytoplankton. See the difference</text>
    <text x="1577" y="1216" textLength="284" lengthAdjust="spacingAndGlyphs">for yourself and understand why</text>
    <text x="1577" y="1245" textLength="271" lengthAdjust="spacingAndGlyphs">it's not just a supplement, but a</text>
    <text x="1577" y="1274" textLength="241" lengthAdjust="spacingAndGlyphs">revolution in pet health and</text>
    <text x="1577" y="1303" textLength="62" lengthAdjust="spacingAndGlyphs">vitality.</text>
  </g>

  <text class="panel-id" x="1790" y="1985" text-anchor="middle">C9</text>
</svg>
</body>
</html>
```